Company Mission & Values Poster

I'd like an A2 Portrait Poster displaying our company's Mission & Values.
See our website for our logo, fonts, mission & values.
https://valdintor.com.au/

Our Mission: Creating homes for abundant life
Values: Love, Thinking, Team, Zoe.

Some ideas to consider:
Mission as the Headline then
A logo for each of the 4 Values and the words

Target Market(s)

Myself & my team

Industry/Entity Type

Real Estate

Font styles to use
Other font styles liked:
• Company fonts as seen on our website

```html
<!DOCTYPE html>
<html lang="en">
<head>
<meta charset="utf-8">
<title>Valdintor – Mission &amp; Core Values Poster</title>
<link rel="stylesheet" href="https://fonts.googleapis.com/css2?family=Cinzel:wght@400;700;900&family=Montserrat:wght@400;500&family=Oswald:wght@500;600&display=swap">
<style>
  :root {
    --ink: #212322;
    --teal: #17d4b5;
    --deep-green: #062e2a;
    --text: #1f2523;
    --label: #0c3b36;
    --mint: #e3f6f1;
    --paper: #ffffff;
    --map-grey: #e6e7e7;
  }
  * { box-sizing: border-box; margin: 0; padding: 0; }
  html, body { width: 730px; height: 1200px; overflow: hidden; background: var(--paper); }
  .poster { position: relative; width: 730px; height: 1200px; overflow: hidden; background: var(--paper); font-family: "Montserrat", sans-serif; }
  .poster-shapes { position: absolute; inset: 0; }

  .map-backdrop {
    position: absolute; left: 20px; top: 930px; width: 690px; height: 270px;
    background: radial-gradient(ellipse at 50% 50%, var(--map-grey) 0%, #eeefef 45%, rgba(255,255,255,0) 75%);
  }

  .value-column {
    position: absolute; top: 600px; height: 360px; width: 164px;
    background: linear-gradient(180deg, rgba(255,255,255,0) 0%, var(--mint) 35%, var(--mint) 60%, rgba(255,255,255,0) 100%);
  }

  .mission { position: absolute; left: 58px; top: 68px; display: flex; align-items: center; }
  .mission-title { font-family: "Cinzel", serif; line-height: 0.9; text-align: left; }
  .mission-title .our { display: block; color: var(--teal); font-weight: 900; font-size: 46px; }
  .mission-title .word { display: block; color: var(--paper); font-weight: 700; font-size: 25px; }
  .mission-divider { width: 1px; height: 70px; background: var(--paper); margin: 0 12px 0 14px; opacity: .8; position: relative; }
  .mission-divider::after { content: ""; position: absolute; left: 2px; top: 31px; border-left: 5px solid var(--teal); border-top: 4px solid transparent; border-bottom: 4px solid transparent; }
  .mission-text { width: 490px; color: var(--paper); font-size: 14.4px; line-height: 17.5px; }

  .headline { position: absolute; left: 0; width: 730px; text-align: center; font-family: "Cinzel", serif; }
  .headline-core { top: 196px; color: var(--teal); font-weight: 900; font-size: 140px; line-height: 1; letter-spacing: -2px; }
  .headline-values { top: 324px; color: var(--paper); font-weight: 700; font-size: 72px; line-height: 1; letter-spacing: 26px; padding-left: 26px; }

  .value { position: absolute; width: 164px; text-align: center; }
  .value-name { font-family: "Oswald", sans-serif; font-weight: 600; font-size: 27px; line-height: 1; color: var(--label); letter-spacing: -0.5px; }
  .value-dots { display: block; margin: 5px auto 10px; width: 18px; height: 3px;
    background: radial-gradient(circle, var(--teal) 1.3px, transparent 1.6px) 0 0 / 4.5px 3px repeat-x; }
  .value-text { font-size: 13.6px; line-height: 16.4px; color: var(--text); padding: 0 8px; }

  .brand { position: absolute; left: 0; width: 730px; top: 1115px; text-align: center;
    font-family: "Montserrat", sans-serif; font-weight: 500; font-size: 28px; letter-spacing: 1px; color: var(--paper); }
</style>
</head>
<body>
<main class="poster">
  <div class="value-column" style="left:34px"></div>
  <div class="value-column" style="left:200px"></div>
  <div class="value-column" style="left:367px"></div>
  <div class="value-column" style="left:533px"></div>

  <div class="map-backdrop" role="img" aria-label="Faint world map in the background"></div>

  <svg class="poster-shapes" width="730" height="1200" viewBox="0 0 730 1200" aria-hidden="true">
    <path class="header-dome" d="M0 0 H730 V205 C700 395 545 514 365 514 C185 514 30 395 0 205 Z" fill="var(--ink)"/>
    <path class="accent-arc" d="M113 456 Q365 660 616 456" fill="none" stroke="var(--teal)" stroke-width="3.5"/>
    <path class="timeline-arc" d="M46 466 Q117 530 200 580 Q283 613 365 612 Q449 613 530 580 Q616 530 690 460" fill="none" stroke="var(--ink)" stroke-width="3.5"/>

    <g class="value-badge" transform="translate(117 541)">
      <path d="M-38 -22 A44 44 0 0 0 -20 38" fill="none" stroke="var(--ink)" stroke-width="2"/>
      <path d="M38 22 A44 44 0 0 0 20 -38" fill="none" stroke="var(--ink)" stroke-width="2"/>
      <circle r="39" fill="var(--ink)"/><circle r="31" fill="var(--teal)"/>
      <path d="M0 13 C-4 9 -16 2 -16 -6 C-16 -12 -11 -15 -7 -15 C-3 -15 -1 -12 0 -10 C1 -12 3 -15 7 -15 C11 -15 16 -12 16 -6 C16 2 4 9 0 13 Z" fill="var(--paper)"/>
    </g>
    <g class="value-badge" transform="translate(283 611)">
      <path d="M-38 -22 A44 44 0 0 0 -20 38" fill="none" stroke="var(--ink)" stroke-width="2"/>
      <path d="M38 22 A44 44 0 0 0 20 -38" fill="none" stroke="var(--ink)" stroke-width="2"/>
      <circle r="39" fill="var(--ink)"/><circle r="31" fill="var(--teal)"/>
      <g fill="var(--paper)">
        <circle cx="-7" cy="-3" r="8"/><circle cx="3" cy="-8" r="8"/><circle cx="10" cy="-1" r="7"/><circle cx="0" cy="2" r="7"/>
        <circle cx="12" cy="9" r="3"/><circle cx="16" cy="14" r="2"/>
      </g>
    </g>
    <g class="value-badge" transform="translate(449 611)">
      <path d="M-38 -22 A44 44 0 0 0 -20 38" fill="none" stroke="var(--ink)" stroke-width="2"/>
      <path d="M38 22 A44 44 0 0 0 20 -38" fill="none" stroke="var(--ink)" stroke-width="2"/>
      <circle r="39" fill="var(--ink)"/><circle r="31" fill="var(--teal)"/>
      <g fill="var(--paper)">
        <circle cx="-10" cy="-7" r="4"/><circle cx="10" cy="-7" r="4"/><circle cx="0" cy="-9" r="5"/>
        <rect x="-16" y="-2" width="11" height="14" rx="3"/><rect x="5" y="-2" width="11" height="14" rx="3"/>
        <rect x="-6" y="-3" width="12" height="16" rx="3"/>
      </g>
    </g>
    <g class="value-badge" transform="translate(616 544)">
      <path d="M-38 -22 A44 44 0 0 0 -20 38" fill="none" stroke="var(--ink)" stroke-width="2"/>
      <path d="M38 22 A44 44 0 0 0 20 -38" fill="none" stroke="var(--ink)" stroke-width="2"/>
      <circle r="39" fill="var(--ink)"/><circle r="31" fill="var(--teal)"/>
      <g fill="none" stroke="var(--paper)" stroke-width="2.2">
        <line x1="-14" y1="-10" x2="14" y2="-10"/>
        <rect x="-17" y="-13" width="6" height="6" fill="var(--paper)"/><rect x="11" y="-13" width="6" height="6" fill="var(--paper)"/>
        <path d="M-8 -4 L0 14 L8 -4 L0 -8 Z"/><line x1="0" y1="-2" x2="0" y2="8"/>
      </g>
    </g>

    <path class="footer-line" d="M214 1017 Q365 909 516 1017" fill="none" stroke="var(--ink)" stroke-width="3.5"/>
    <path class="footer-accent" d="M157 1122 Q365 868 573 1122" fill="none" stroke="var(--teal)" stroke-width="3"/>
    <path class="footer-dome" d="M151 1200 C160 1090 250 1024 365 1024 C480 1024 570 1090 579 1200 Z" fill="var(--deep-green)"/>
  </svg>

  <section class="mission">
    <h2 class="mission-title"><span class="our">OUR</span><span class="word">MISSION</span></h2>
    <span class="mission-divider"></span>
    <p class="mission-text">We wholeheartedly believe that home is an extraordinary place: a haven where life unfolds in all its glory. Where we find solace, make cherished memories with loved ones, and savour the&nbsp; natural beauty that surrounds us.</p>
  </section>

  <h1>
    <span class="headline headline-core">CORE</span>
    <span class="headline headline-values">VALUES</span>
  </h1>

  <article class="value" style="left:34px; top:632px">
    <h3 class="value-name">LOVE</h3><span class="value-dots"></span>
    <p class="value-text">Our mission is founded in our love and respect for people - those we develop for, those in our teams and those in the communities we create and operate within.</p>
  </article>
  <article class="value" style="left:200px; top:694px">
    <h3 class="value-name">THINKING</h3><span class="value-dots"></span>
    <p class="value-text">We believe in the power of thinking. Our rigorous and creative processes create beautifully considered solutions for our purchasers, the communities we develop within and the environment.</p>
  </article>
  <article class="value" style="left:367px; top:694px">
    <h3 class="value-name">TEAM</h3><span class="value-dots"></span>
    <p class="value-text">Property development is a team sport. We surround ourselves with the best designers and advisers. We strive to create an environment that allows them to do their best work and love doing it.</p>
  </article>
  <article class="value" style="left:533px; top:628px">
    <h3 class="value-name">ZOE</h3><span class="value-dots"></span>
    <p class="value-text">Our mission is to create places for ‘Zoe’ – the Greek word for abundant life. We do this through exquisite design, quality construction and celebrating nature.</p>
  </article>

  <p class="brand">Valdintor</p>
</main>
</body>
</html>
```